I need a letterhead for a newsletter that will go out quarterly to the dentists of the 18th district. It is called "The Crestline Digest" We are in Amarillo TX and have this landmark in the photo as our most prominent feature. If it could be used, that would be cool.
This is a professional organization newsletter so the letterhead should be somewhat professional.

Target Market(s)

Dentists

Industry/Entity Type

Dental

Font styles to use
Serif

Colors

Designer to choose only greyscale colors for use in the design.

Requirements
Must have
• I want the title of "The Crestline Digest" to be the on top with the phrase "Cobalt Ridge Dental Society" written underneath.
Nice to have
• the photo incorporated could be incorporated in black and white or color along the bottom of the letterhead or with the title inside the photo.
Should not have
• I don't want it to be cartoony. I want it to be stylish and elegant and professional.

```html
<!DOCTYPE html>
<html lang="en">
<head>
<meta charset="utf-8">
<title>The Crestline Digest – Letterhead</title>
<link href="https://fonts.googleapis.com/css2?family=Cinzel:wght@400;500&family=Didact+Gothic&family=Lato:wght@400&display=swap" rel="stylesheet">
<style>
  :root {
    --backdrop: #e3e3e3;
    --paper: #ffffff;
    --band: #4a4a4a;
    --ink: #3a3a3a;
    --on-band: #ffffff;
    --on-band-soft: #e2e2e2;
    --photo-dark: #2e2e2e;
    --photo-mid: #9c9c9c;
    --photo-low: #5e5e5e;
  }
  * { margin: 0; padding: 0; box-sizing: border-box; }
  html, body {
    width: 1200px; height: 898px; overflow: hidden;
    background: var(--backdrop);
  }
  .letterhead {
    position: absolute; left: 295px; top: 18px;
    width: 610px; height: 862px;
    background: var(--paper);
    box-shadow: 0 6px 24px rgba(0, 0, 0, 0.16);
    overflow: hidden;
  }
  .masthead-band {
    position: absolute; left: 0; right: 0; top: 100px; height: 140px;
    background: var(--band);
  }
  .masthead-photo {
    position: absolute; left: 400px; top: 82px; width: 180px; height: 172px;
    border-radius: 26px;
    background: linear-gradient(160deg, var(--photo-dark) 0%, var(--photo-mid) 45%, #7a7a7a 62%, var(--photo-low) 100%);
  }
  .masthead-text {
    position: absolute; right: 228px; top: 118px; width: 340px;
    text-align: right; color: var(--on-band);
  }
  .title {
    font-family: "Cinzel", serif; font-weight: 500;
    font-size: 29px; letter-spacing: 0.5px; line-height: 1.1;
  }
  .society {
    font-family: "Cinzel", serif; font-size: 13.5px;
    letter-spacing: 0.6px; margin-top: 8px;
  }
  .address {
    font-family: "Lato", sans-serif; font-size: 11px; margin-top: 12px;
  }
  .contact-row {
    display: flex; justify-content: flex-end; gap: 18px;
    font-family: "Lato", sans-serif; font-size: 11px;
    color: var(--on-band-soft); margin-top: 10px;
  }
  .contact-item { display: flex; align-items: center; gap: 5px; }
  .contact-item svg { width: 10px; height: 10px; fill: var(--on-band-soft); }
  .letter-body {
    position: absolute; left: 110px; top: 330px; width: 420px;
    font-family: "Didact Gothic", sans-serif; font-size: 12.5px;
    line-height: 1.95; color: var(--ink);
  }
  .salutation { margin-bottom: 14px; }
  .letter-body p + p { margin-top: 22px; }
  .signature { margin-top: 22px; }
  .signer-name { font-size: 17px; color: var(--ink); }
  .signer-role { font-size: 11.5px; margin-top: 2px; }
  .footer-rule {
    position: absolute; left: 0; right: 0; bottom: 0; height: 6px;
    background: var(--band);
  }
</style>
</head>
<body>
  <main class="letterhead">
    <div class="masthead-band"></div>
    <div class="masthead-photo" role="img" aria-label="Black and white photograph of a sandstone canyon landmark under an open sky"></div>
    <header class="masthead-text">
      <h1 class="title">The Crestline Digest</h1>
      <div class="society">Cobalt Ridge Dental Society</div>
      <div class="address">418 Mesa Crest Ave, Cobalt Ridge, Larkin County 79110, USA</div>
      <div class="contact-row">
        <span class="contact-item">
          <svg viewBox="0 0 24 24"><path d="M6.6 10.8a15.1 15.1 0 0 0 6.6 6.6l2.2-2.2c.3-.3.7-.4 1-.2 1.1.4 2.3.6 3.6.6.6 0 1 .4 1 1V20c0 .6-.4 1-1 1C10.6 21 3 13.4 3 4c0-.6.4-1 1-1h3.5c.6 0 1 .4 1 1 0 1.3.2 2.5.6 3.6.1.3 0 .7-.2 1z"/></svg>
          806.555.0147
        </span>
        <span class="contact-item">
          <svg viewBox="0 0 24 24"><path d="M12 2a10 10 0 1 0 0 20 10 10 0 0 0 0-20zm6.9 6h-3a15.7 15.7 0 0 0-1.3-4 8 8 0 0 1 4.3 4zM12 4c.8 1.2 1.5 2.5 1.9 4h-3.8c.4-1.5 1.1-2.8 1.9-4zM4.3 14a8 8 0 0 1 0-4h3.4a16.5 16.5 0 0 0 0 4zm.8 2h3a15.7 15.7 0 0 0 1.3 4 8 8 0 0 1-4.3-4zm3-8h-3a8 8 0 0 1 4.3-4A15.7 15.7 0 0 0 8.1 8zM12 20c-.8-1.2-1.5-2.5-1.9-4h3.8c-.4 1.5-1.1 2.8-1.9 4zm2.3-6H9.7a14.7 14.7 0 0 1 0-4h4.6a14.7 14.7 0 0 1 0 4zm.3 6a15.7 15.7 0 0 0 1.3-4h3a8 8 0 0 1-4.3 4zm1.7-6a16.5 16.5 0 0 0 0-4h3.4a8 8 0 0 1 0 4z"/></svg>
          www.cobaltridgedental.org
        </span>
      </div>
    </header>

    <section class="letter-body">
      <div class="salutation">Hello Sir/Mam,</div>
      <p>Lorem ipsum dolor sit amet, consectetur adipiscing elit. Donec orci purus, luctus vitae dignissim eu, iaculis sed purus. Vivamus faucibus, ipsum nec aliquet viverra, leo mauris condimentum ligula, sit amet sagittis enim ligula quis arcu. Nam egestas tortor id nisi porttitor mattis. In tortor ante, ultricies in suscipit a, tempus non massa. Vivamus et auctor mi. Fusce vel massa nulla. Phasellus nec eros mauris, et scelerisque orci. Donec malesuada orci vitae nulla accumsan porta a id massa.</p>
      <p>Quisque accumsan iaculis magna sit amet fringilla. Maecenas consequat, magna eget tincidunt semper, odio nibh rutrum mi, id feugiat ante nisi eu risus. Vestibulum nunc orci, rhoncus a placerat in, ultricies in mi. Cras mattis varius eros, vel fringilla nisi suscipit eget. Quisque scelerisque sagittis nulla at porttitor. Mauris a justo et tellus interdum tristique. Sed id augue vitae urna euismod commodo aliquet a quam. Pellentesque arcu velit, cursus et malesuada ut, consequat et diam. Nullam erat sem, rhoncus id ullamcorper vitae, rhoncus et arcu. In ultricies ultricies nulla.</p>
      <div class="signature">
        <div class="signer-name">Elliot Marsh</div>
        <div class="signer-role">Co-Founder &amp; CEO</div>
      </div>
    </section>

    <div class="footer-rule"></div>
  </main>
</body>
</html>
```